Business card for Luxury Portable Restroom Trailer company

We are a Luxury Portable Restroom Trailer Company Called FALCRIDGE HIRES. Based in Orange County California. We provide portable restroom trailers for events, such as, Weddings, Concerts, Charity events, Sporting events, Tournaments, Corporate events, ect. We rent and Sell the Luxury restrooms. Our colors are white, grey, and Orange. As you will see in the logo we uploaded.
There are 2 people in the company so the names and titles will change for the 3 people but card will remain the same. Here is the information for each Person: Dwight Penner CFO 555 318-0476
next Person: Leon Marchetti VP 555 318-0476
Next Person: Owen Marchetti CEO 555 318-0476
Information to include on the card: Luxury Restroom Trailers Rental and Sales. Weddings, Concerts, Charity, Sporting and Corp. Events.

```html
<!DOCTYPE html>
<html lang="en">
<head>
<meta charset="utf-8">
<title>FALCRIDGE HIRES – Business Card</title>
<link rel="stylesheet" href="https://fonts.googleapis.com/css2?family=Montserrat:wght@400;500;700;800&display=swap">
<style>
  :root {
    --orange: #f26b23;
    --white: #ffffff;
    --grey: #55565a;
    --ink: #2b2b2d;
    --backdrop: #d9d9d9;
  }
  * { box-sizing: border-box; margin: 0; padding: 0; }
  html, body { width: 1200px; height: 856px; overflow: hidden; }
  body {
    background: var(--backdrop);
    font-family: "Montserrat", sans-serif;
    position: relative;
  }
  .card {
    position: absolute;
    top: 273px;
    width: 540px;
    height: 310px;
    overflow: hidden;
    box-shadow: 0 10px 24px rgba(0,0,0,.25);
  }
  .card--front { left: 40px; background: var(--white); }
  .card--back { left: 620px; background: var(--orange); color: var(--white); }

  .front-band { position: absolute; inset: 0; width: 100%; height: 100%; }

  .brand-ring {
    position: absolute;
    left: 38px; top: 64px;
    width: 182px; height: 182px;
    border: 9px solid var(--orange);
    border-radius: 50%;
    display: flex; align-items: center; justify-content: center;
  }
  .brand-ring__name {
    font-weight: 800;
    color: var(--orange);
    font-size: 17px;
    line-height: 1.15;
    text-align: center;
    letter-spacing: .5px;
  }

  .divider {
    position: absolute;
    left: 262px; top: 50px;
    width: 2px; height: 196px;
    background: var(--orange);
  }

  .team { position: absolute; left: 284px; top: 44px; list-style: none; }
  .member { margin-bottom: 12px; }
  .member__name {
    font-weight: 800;
    font-size: 16px;
    letter-spacing: .4px;
    text-transform: uppercase;
    color: var(--grey);
  }
  .member__name .surname { color: var(--orange); }
  .member__title { font-size: 12px; font-weight: 500; color: var(--ink); margin-top: 1px; }
  .member__phone {
    display: flex; align-items: center; gap: 6px;
    font-size: 12px; font-weight: 500; color: var(--ink); margin-top: 2px;
  }
  .member__phone svg { width: 13px; height: 13px; fill: var(--orange); }

  .back-brand {
    position: absolute;
    left: 0; right: 0; top: 92px;
    text-align: center;
    font-weight: 800;
    font-size: 40px;
    letter-spacing: 2px;
  }
  .services {
    position: absolute;
    left: 0; right: 0; top: 198px;
    text-align: center;
    font-size: 13.5px;
    font-weight: 500;
    line-height: 1.7;
  }
  .services .dot {
    display: inline-block;
    width: 7px; height: 7px;
    border-radius: 50%;
    background: var(--white);
    margin: 0 6px 2px;
    vertical-align: middle;
  }
</style>
</head>
<body>

<section class="card card--front" aria-label="Card front">
  <svg class="front-band" viewBox="0 0 540 310" preserveAspectRatio="none" aria-hidden="true">
    <polygon points="318,310 330,284 540,284 540,310" fill="var(--orange)"/>
  </svg>

  <div class="brand-ring">
    <span class="brand-ring__name">FALCRIDGE<br>HIRES</span>
  </div>

  <div class="divider"></div>

  <ul class="team">
    <li class="member">
      <div class="member__name">Dwight <span class="surname">Penner</span></div>
      <div class="member__title">CFO</div>
      <div class="member__phone">
        <svg viewBox="0 0 24 24" aria-hidden="true"><path d="M6.6 10.8a15.1 15.1 0 0 0 6.6 6.6l2.2-2.2a1 1 0 0 1 1-.25 11.4 11.4 0 0 0 3.6.57 1 1 0 0 1 1 1V20a1 1 0 0 1-1 1A17 17 0 0 1 3 4a1 1 0 0 1 1-1h3.5a1 1 0 0 1 1 1c0 1.25.2 2.45.57 3.57a1 1 0 0 1-.25 1z"/></svg>
        555 318-0476
      </div>
    </li>
    <li class="member">
      <div class="member__name">Leon <span class="surname">Marchetti</span></div>
      <div class="member__title">VP</div>
      <div class="member__phone">
        <svg viewBox="0 0 24 24" aria-hidden="true"><path d="M6.6 10.8a15.1 15.1 0 0 0 6.6 6.6l2.2-2.2a1 1 0 0 1 1-.25 11.4 11.4 0 0 0 3.6.57 1 1 0 0 1 1 1V20a1 1 0 0 1-1 1A17 17 0 0 1 3 4a1 1 0 0 1 1-1h3.5a1 1 0 0 1 1 1c0 1.25.2 2.45.57 3.57a1 1 0 0 1-.25 1z"/></svg>
        555 318-0476
      </div>
    </li>
    <li class="member">
      <div class="member__name">Owen <span class="surname">Marchetti</span></div>
      <div class="member__title">CEO</div>
      <div class="member__phone">
        <svg viewBox="0 0 24 24" aria-hidden="true"><path d="M6.6 10.8a15.1 15.1 0 0 0 6.6 6.6l2.2-2.2a1 1 0 0 1 1-.25 11.4 11.4 0 0 0 3.6.57 1 1 0 0 1 1 1V20a1 1 0 0 1-1 1A17 17 0 0 1 3 4a1 1 0 0 1 1-1h3.5a1 1 0 0 1 1 1c0 1.25.2 2.45.57 3.57a1 1 0 0 1-.25 1z"/></svg>
        555 318-0476
      </div>
    </li>
  </ul>
</section>

<section class="card card--back" aria-label="Card back">
  <div class="back-brand">FALCRIDGE HIRES</div>
  <p class="services">
    <span class="dot"></span>Luxury Restroom Trailers Rental and Sales<br>
    <span class="dot"></span>Weddings <span class="dot"></span>Concerts <span class="dot"></span>Charity <span class="dot"></span>Sporting and Corp <span class="dot"></span>Events
  </p>
</section>

</body>
</html>
```